Business card design Needed for new logo / Construction business, home extensions and new builds

We need a business card design using our new logo files which i will attach to this project :)

We are a small construction business specialising in home extensions, new builds and property development. We are very ambitious and would appreciate professional and elegant designs for our new business card.

Very serious about using the services on MakerQuarry and recently acquired our new logo from here :)

Please get involved, i will feedback when i can as i am very busy but can respond daily, thanks

Target Market(s)

People that want to build onto their houses, new building developments or adding too their existing property

Industry/Entity Type

Construction

Contact Information for Business Card

Renwick Tolliver Construction, Lionel Ashby (Managing Director), Tel 07822254961, email - info@renwick-tolliver, www.renwick-tolliver.co.uk

Colors

Designer to choose colors to be used in the design.

Requirements
Must have
• I like a deep grey on the back please. A lot of you have provided black from and back, try mixing things up a little. The black looks cool 😎 Thanks

```html
<!DOCTYPE html>
<html lang="en">
<head>
<meta charset="utf-8">
<title>Renwick Tolliver Construction – Business Card</title>
<link rel="stylesheet" href="https://fonts.googleapis.com/css2?family=Open+Sans:wght@400;600;700&display=swap">
<style>
  :root {
    --backdrop: #222223;
    --card-deep: #1e1e20;
    --card-back-top: #2c2c2f;
    --card-back-bottom: #151516;
    --gold: #d9a634;
    --gold-light: #f2c85b;
    --silver: #c9cacc;
    --ink: #f4f4f4;
    --rule: #8d8e91;
  }
  * { box-sizing: border-box; margin: 0; padding: 0; }
  html, body {
    width: 1200px; height: 780px; overflow: hidden;
    background: var(--backdrop);
    font-family: "Open Sans", Arial, sans-serif;
  }
  .canvas { position: relative; width: 1200px; height: 780px; }

  .card {
    position: absolute;
    width: 560px; height: 320px;
    border-radius: 3px;
    box-shadow: 0 14px 30px rgba(0,0,0,.55);
    overflow: hidden;
  }

  /* Back of card */
  .card-back { left: 50px; top: 80px; }
  .card-back .pattern-field {
    position: absolute; inset: 0;
    background: linear-gradient(160deg, var(--card-back-top) 0%, #202022 45%, var(--card-back-bottom) 100%);
  }
  .card-back .corner-name {
    position: absolute; right: 26px; bottom: 22px;
    display: flex; align-items: center; gap: 6px;
    font-size: 9px; font-weight: 600; letter-spacing: .08em;
    color: var(--gold); text-transform: uppercase;
  }
  .corner-name .mark-square { width: 7px; height: 7px; background: var(--gold); }

  /* Front of card */
  .card-front {
    left: 590px; top: 380px;
    background: var(--card-deep);
  }
  .brand {
    position: absolute; left: 34px; top: 0; width: 230px; height: 100%;
    display: flex; flex-direction: column; align-items: center; justify-content: center; gap: 12px;
  }
  .brand .mark-square { width: 40px; height: 40px; background: var(--gold); }
  .brand-name {
    text-align: center; color: var(--gold);
    font-weight: 600; font-size: 19px; line-height: 1.3; letter-spacing: .08em;
    text-transform: uppercase;
  }
  .divider {
    position: absolute; left: 285px; top: 62px; width: 1px; height: 196px;
    background: var(--rule);
  }
  .details { position: absolute; left: 310px; top: 62px; color: var(--ink); }
  .person-name { font-size: 23px; font-weight: 700; line-height: 1.1; }
  .person-name .first { color: var(--silver); }
  .person-name .last { color: var(--gold-light); }
  .person-role { font-size: 12px; font-weight: 600; margin-top: 3px; }
  .address { font-size: 11.5px; line-height: 1.45; margin-top: 16px; }
  .contacts { list-style: none; margin-top: 16px; font-size: 11.5px; }
  .contacts li { display: flex; align-items: center; gap: 8px; line-height: 1.7; }
  .contacts svg { width: 12px; height: 12px; flex: none; }
</style>
</head>
<body>
<main class="canvas">

  <section class="card card-back" aria-label="Card back">
    <div class="pattern-field" role="img" aria-label="Repeating monogram pattern in glossy black and grey"></div>
    <div class="corner-name"><span class="mark-square"></span>Renwick Tolliver Construction</div>
  </section>

  <section class="card card-front" aria-label="Card front">
    <div class="brand">
      <span class="mark-square"></span>
      <p class="brand-name">Renwick Tolliver<br>Construction</p>
    </div>
    <div class="divider"></div>
    <div class="details">
      <h1 class="person-name"><span class="first">Lionel</span> <span class="last">Ashby</span></h1>
      <p class="person-role">Managing Director</p>
      <p class="address">Hollins Lane, Ashcombe<br>Bramwell, BR4 7KD</p>
      <ul class="contacts">
        <li>
          <svg viewBox="0 0 24 24" fill="var(--gold)"><path d="M6.6 10.8a15.1 15.1 0 0 0 6.6 6.6l2.2-2.2c.3-.3.7-.4 1-.2 1.1.4 2.3.6 3.6.6.6 0 1 .4 1 1V20c0 .6-.4 1-1 1A17 17 0 0 1 3 4c0-.6.4-1 1-1h3.5c.6 0 1 .4 1 1 0 1.3.2 2.5.6 3.6.1.3 0 .7-.2 1z"/></svg>
          0782 225 4961
        </li>
        <li>
          <svg viewBox="0 0 24 24" fill="none" stroke="var(--gold)" stroke-width="2"><rect x="3" y="5" width="18" height="14" rx="1"/><path d="M3 6l9 7 9-7"/></svg>
          info@renwick-tolliver.co.uk
        </li>
        <li>
          <svg viewBox="0 0 24 24" fill="none" stroke="var(--gold)" stroke-width="2"><circle cx="12" cy="12" r="9"/><path d="M3 12h18M12 3c3 3 3 15 0 18M12 3c-3 3-3 15 0 18"/></svg>
          www.renwick-tolliver.co.uk
        </li>
      </ul>
    </div>
  </section>

</main>
</body>
</html>
```